Fitness Equipment Repair Business Needs a Catchy New Business Card

We have an existing business card, however, it is quite plain and boring. We are expanding primarily in the commercial area (gyms, studios, apartment complexes etc). The business card will serve as eye candy to those managers/owners that can't be met for a face to face.
Originally I was planning for a brochure as well, but all of our information is better summarized on our website. (brightloopservice.ca).
I would like the card to match the colour scheme of the website and utilize the logo. It should have a professional clean feel to it, however, a little colouring outside the lines wouldn't hurt.
The example card is for my service technician (Colin Marsh). If possible I would like to be able to edit the text to use for more than one person.

Industry/Entity Type

Appliance Repair

Contact Information for Business Card

Clean, crisp and professional but needs to be eye catching. Preferably using the black, white and red colour scheme matching the website. Double sided would be nice, but is not necessary.

Colors
ec1f27
ffffff
000000

Requirements
Must have
• Must be able to edit name, phone number and title to use for multiple people. Must show the company website (brightloopservice.ca).

```html
<!DOCTYPE html>
<html lang="en">
<head>
<meta charset="utf-8">
<title>Bright Loop Service – Business Card</title>
<link rel="stylesheet" href="https://fonts.googleapis.com/css2?family=Marcellus+SC&family=Open+Sans:ital,wght@0,400;0,600;1,700&display=swap">
<style>
  :root {
    --brand-red: #ec1f27;
    --ink-black: #000000;
    --paper-white: #ffffff;
    --stage: #e4e2df;
    --display-font: "Marcellus SC", serif;
    --body-font: "Open Sans", sans-serif;
  }
  * { box-sizing: border-box; margin: 0; padding: 0; }
  html, body { width: 1200px; height: 987px; overflow: hidden; }
  body { background: var(--stage); position: relative; font-family: var(--body-font); }

  .card { position: absolute; left: 293px; width: 615px; }

  /* Front side */
  .card-front { top: 131px; height: 349px; background: var(--paper-white); }
  .front-main { position: absolute; left: 0; top: 0; width: 100%; height: 318px; background: var(--ink-black); }
  .tagline-band {
    position: absolute; left: 0; bottom: 0; width: 100%; height: 28px;
    background: var(--brand-red); color: var(--paper-white);
    font: italic 700 14.5px/28px var(--body-font); text-align: center;
  }
  .brand-lockup { position: absolute; left: 48px; top: 140px; display: flex; align-items: center; gap: 14px; }
  .brand-dot { width: 52px; height: 52px; border-radius: 50%; background: var(--brand-red); }
  .brand-name { font-family: var(--display-font); font-size: 18px; color: var(--paper-white); letter-spacing: .5px; }

  .person { position: absolute; left: 355px; top: 52px; color: var(--paper-white); }
  .person-name { font-family: var(--display-font); font-size: 23px; color: var(--brand-red); line-height: 28px; letter-spacing: 1px; }
  .person-title { font-family: var(--display-font); font-size: 16.5px; line-height: 20px; letter-spacing: 1px; }
  .address { margin-top: 16px; font-size: 15px; line-height: 22px; }
  .contacts { list-style: none; margin-top: 14px; font-size: 14.5px; }
  .contacts li { display: flex; align-items: center; gap: 8px; height: 23.5px; }
  .contacts svg { width: 14px; height: 14px; fill: var(--brand-red); flex: none; }
  .contact-note { font-size: 11.5px; }

  /* Back side */
  .card-back { top: 506px; height: 351px; background: var(--brand-red); color: var(--paper-white); text-align: center; }
  .back-lockup { position: absolute; left: 0; top: 92px; width: 100%; display: flex; flex-direction: column; align-items: center; gap: 18px; }
  .back-dot { width: 96px; height: 96px; border-radius: 50%; background: var(--paper-white); }
  .back-name { font-family: var(--display-font); font-size: 30px; letter-spacing: 1px; }
  .back-web { position: absolute; left: 0; top: 302px; width: 100%; font-family: var(--display-font); font-size: 16px; letter-spacing: 2.5px; }
</style>
</head>
<body>

<section class="card card-front">
  <div class="front-main">
    <div class="brand-lockup">
      <span class="brand-dot"></span>
      <span class="brand-name">Bright Loop Service</span>
    </div>

    <div class="person">
      <p class="person-name">Colin Marsh</p>
      <p class="person-title">Service technician</p>
      <p class="address">1875 Carver Lane NW<br>Edmonton AB T5K 2P4</p>
      <ul class="contacts">
        <li><svg viewBox="0 0 16 16"><path d="M3.6 1 6 3.4 4.8 5.6c.9 2.2 3.4 4.7 5.6 5.6L12.6 10 15 12.4 13 15C7 14.4 1.6 9 1 3z"/></svg><span>587-555-0148<span class="contact-note">(Personal)</span></span></li>
        <li><svg viewBox="0 0 16 16"><path d="M3.6 1 6 3.4 4.8 5.6c.9 2.2 3.4 4.7 5.6 5.6L12.6 10 15 12.4 13 15C7 14.4 1.6 9 1 3z"/></svg><span>780-555-0193<span class="contact-note">(Service Line)</span></span></li>
        <li><svg viewBox="0 0 16 16"><path d="M1 3h14v10H1z M1 3l7 6 7-6" fill="var(--brand-red)" stroke="var(--ink-black)" stroke-width="1.2"/></svg><span>hello@brightloopservice.ca</span></li>
        <li><svg viewBox="0 0 16 16"><circle cx="8" cy="8" r="7"/><path d="M1 8h14M8 1c-3 3-3 11 0 14M8 1c3 3 3 11 0 14" fill="none" stroke="var(--ink-black)" stroke-width="1"/></svg><span>brightloopservice.ca</span></li>
      </ul>
    </div>
  </div>
  <p class="tagline-band">When Your Equipment Can't Finish The Workout, Give Us A Call!</p>
</section>

<section class="card card-back">
  <div class="back-lockup">
    <span class="back-dot"></span>
    <span class="back-name">Bright Loop Service</span>
  </div>
  <p class="back-web">WWW.BRIGHTLOOPSERVICE.CA</p>
</section>

</body>
</html>
```